4th Generation Family Business Needs a New Card Design!

We are a family owned 4th Generation company. We are based in the Sydney, Australia area and we are desperately in need of a more modern and classy card. We are monumental masons who design, supply & erect lasting memorials throughout cemeteries in Sydney. Our customers are normally in a period of grieving. I have attached logo files that will need to be implemented on the card. Company was established 1935. Australian Owned and Operated. Card needs to be designed to PIXO.com specification.

Target Market(s)

Our target market is based upon people that a grieving for family members that have passed away. We also deal with alot of companies that own and operate cemeteries.

Industry/Entity Type

Business

Contact Information for Business Card

Simon Harcourt, Operations Manager, 0417293086, simon@harcourtmemorials.com.au
Lewis Harcourt, Director, 0491630572, lewis@harcourtmemorials.com.au
Phone # 02 9561 3048
Website: www.harcourtmemorials.com.au
Address: Suite 17, 8 Palfrey Lane, West Carlow, Sydney NSW 2156

Font styles to use
Serif
Decorative
Script

Requirements
Must have
• Would like to see the logo nicely implemented with a modern design. Embossed lettering would be a nice additive.

```html
<!DOCTYPE html>
<html lang="en">
<head>
<meta charset="utf-8">
<title>Harcourt Memorials – Business Card</title>
<link rel="stylesheet" href="https://fonts.googleapis.com/css2?family=Cinzel:wght@400;600&family=Open+Sans:wght@400;600&display=swap">
<style>
  :root {
    --stage: #d9d9d9;
    --charcoal: #252323;
    --charcoal-tint: #2e2b2b;
    --ink: #1d1b1b;
    --gold: #e8b923;
    --grey-text: #6b6b6b;
    --paper: #ffffff;
    --serif: "Cinzel", "Times New Roman", serif;
    --sans: "Open Sans", Arial, sans-serif;
  }
  * { margin: 0; padding: 0; box-sizing: border-box; }
  html, body { width: 1200px; height: 950px; overflow: hidden; }
  body { background: var(--stage); position: relative; font-family: var(--sans); }

  .card {
    position: absolute;
    width: 620px;
    height: 379px;
    overflow: hidden;
    box-shadow: 0 6px 18px rgba(0,0,0,0.18);
  }

  /* Back of card */
  .card-back {
    left: 170px; top: 60px;
    background: var(--charcoal);
    color: var(--paper);
  }
  .card-back .backdrop-square {
    position: absolute; left: 190px; top: 40px;
    width: 300px; height: 300px;
    background: var(--charcoal-tint);
  }
  .card-back .brand {
    position: absolute; left: 0; right: 0; top: 140px;
    text-align: center;
  }
  .card-back .brand-name {
    font-family: var(--serif); font-weight: 400;
    font-size: 44px; letter-spacing: 2px; line-height: 1;
    color: var(--paper);
  }
  .card-back .website {
    margin-top: 22px;
    font-size: 15px; letter-spacing: 2px; color: var(--paper);
  }

  /* Front of card */
  .card-front {
    left: 410px; top: 500px;
    background: var(--paper);
    color: var(--ink);
  }
  .card-front .brand {
    position: absolute; left: 30px; top: 150px; width: 270px;
    text-align: center;
  }
  .card-front .brand-name {
    font-family: var(--serif); font-weight: 400;
    font-size: 36px; line-height: 1.05; letter-spacing: 1px;
    color: var(--ink);
  }

  .contact {
    position: absolute; left: 330px; top: 44px; width: 270px;
  }
  .contact .person {
    font-family: var(--serif); font-weight: 600;
    font-size: 19px; letter-spacing: 1px; color: var(--ink);
  }
  .contact .role {
    font-family: var(--serif); font-size: 13px; letter-spacing: 1px;
    color: var(--gold); margin-top: 2px;
  }
  .contact .address {
    margin-top: 14px; font-size: 12.5px; line-height: 1.5; color: var(--grey-text);
  }
  .contact .lines { list-style: none; margin-top: 10px; }
  .contact .lines li {
    display: flex; align-items: center; gap: 8px;
    font-size: 12.5px; line-height: 1.75; color: var(--grey-text);
  }
  .contact .lines svg { width: 12px; height: 12px; fill: var(--ink); flex: none; }

  .accent-band { position: absolute; left: 0; top: 0; width: 620px; height: 379px; }
  .corner-name {
    position: absolute; right: 14px; top: 251px;
    font-family: var(--serif); font-size: 10px; letter-spacing: 0.5px; color: var(--ink);
  }
  .footer-band {
    position: absolute; left: 0; right: 0; bottom: 0; height: 58px;
    background: var(--ink);
    display: flex; align-items: center; padding-left: 150px;
    color: var(--paper); font-size: 15px; letter-spacing: 1px;
  }
</style>
</head>
<body>

  <section class="card card-back" aria-label="Business card back">
    <div class="backdrop-square" aria-hidden="true"></div>
    <div class="brand">
      <div class="brand-name">HARCOURT MEMORIALS</div>
      <div class="website">www.harcourtmemorials.com.au</div>
    </div>
  </section>

  <section class="card card-front" aria-label="Business card front">
    <svg class="accent-band" viewBox="0 0 620 379" aria-hidden="true">
      <polygon points="520,232 620,232 620,280 490,280" fill="var(--gold)"/>
    </svg>
    <div class="corner-name">HARCOURT</div>

    <div class="brand">
      <div class="brand-name">HARCOURT<br>MEMORIALS</div>
    </div>

    <div class="contact">
      <div class="person">SIMON HARCOURT</div>
      <div class="role">OPERATIONS MANAGER</div>
      <div class="address">Suite 17, 8 Palfrey Lane<br>West Carlow, Sydney NSW 2156</div>
      <ul class="lines">
        <li>
          <svg viewBox="0 0 12 12" aria-hidden="true"><path d="M2.4 1 4.2 2.8 3.3 4.3c.7 1.6 2.1 3 4.4 4.4l1.5-.9L11 9.6 9.7 11C5.3 10.6 1.4 6.7 1 2.3z"/></svg>
          02 9561 3048
        </li>
        <li>
          <svg viewBox="0 0 12 12" aria-hidden="true"><path d="M3.5 0.5h5a1 1 0 0 1 1 1v9a1 1 0 0 1-1 1h-5a1 1 0 0 1-1-1v-9a1 1 0 0 1 1-1zm.3 1.3v7.4h4.4V1.8z"/></svg>
          0417293086
        </li>
        <li>
          <svg viewBox="0 0 12 12" aria-hidden="true"><path d="M1 3h10v7H1zm1.2 1.1v4.8h7.6V4.1zM3.4 6l1.1-1 1.2 1.2 2.5-2.5 1 1-3.5 3.5z"/></svg>
          simon@harcourtmemorials.com.au
        </li>
      </ul>
    </div>

    <div class="footer-band">www.harcourtmemorials.com.au</div>
  </section>

</body>
</html>
```